Corvane Card

The logo is the Spanish flag colors I want a vibrant eye catching design with the yellow / red colors over either Navy or white background or black even ,
Would like a 2D feel to the logo with another lighter color logo under it look ,

Contact Information for Business Card

Corvane Flooring
Teodor Vashkin
Main Number
Cell Number
Fax Number

Website on the side of the card somewhere

Font styles to use
Sans Serif

Colors
ec1f27
ffc214

Requirements
Must have
• 2 logos feel one is bolder and the other one underneath very light

```html
<!DOCTYPE html>
<html lang="en">
<head>
<meta charset="utf-8">
<title>Corvane Card</title>
<link rel="stylesheet" href="https://fonts.googleapis.com/css2?family=Syncopate:wght@700&family=Arimo:wght@400&display=swap">
<style>
  :root {
    --backdrop: #2b2b2e;
    --navy: #05052a;
    --navy-deep: #03031c;
    --navy-pattern: #0d0f4a;
    --red: #ec1f27;
    --yellow: #ffc214;
    --white: #ffffff;
    --divider: #3a3c5c;
  }
  * { box-sizing: border-box; margin: 0; padding: 0; }
  html, body { width: 1200px; height: 1015px; overflow: hidden; }
  body {
    background: var(--backdrop);
    font-family: "Arimo", Arial, sans-serif;
    position: relative;
  }
  .card {
    position: absolute;
    left: 280px;
    width: 640px;
    height: 366px;
    background: var(--navy);
    overflow: hidden;
    box-shadow: 0 14px 34px rgba(0,0,0,0.55);
  }
  .card--back { top: 110px; }
  .card--front { top: 540px; background: var(--navy-deep); }

  .back-texture {
    position: absolute; inset: 0;
    background: radial-gradient(ellipse at 70% 20%, var(--navy-pattern) 0%, var(--navy) 55%, var(--navy-deep) 100%);
  }
  .back-mark {
    position: absolute; left: 50%; top: 50%;
    transform: translate(-50%, -50%);
    display: flex; align-items: center; gap: 8px;
  }
  .brand-square { width: 12px; height: 12px; background: var(--yellow); flex: none; }
  .brand-name {
    font-family: "Syncopate", "Arial Black", sans-serif;
    font-weight: 700;
    color: var(--red);
    letter-spacing: 1px;
    line-height: 1.15;
  }
  .back-mark .brand-name { font-size: 15px; }

  .front-brand {
    position: absolute; left: 40px; top: 140px;
    width: 250px;
    display: flex; align-items: center; gap: 12px;
  }
  .front-brand .brand-square { width: 22px; height: 22px; }
  .front-brand .brand-name { font-size: 24px; }

  .divider {
    position: absolute; left: 325px; top: 70px;
    width: 1px; height: 226px;
    background: linear-gradient(var(--navy-deep), var(--divider), var(--navy-deep));
  }

  .contact { position: absolute; left: 360px; top: 92px; }
  .person-name {
    font-family: "Syncopate", "Arial Black", sans-serif;
    font-weight: 700; font-size: 20px; letter-spacing: 1px;
    margin-bottom: 20px; white-space: nowrap;
  }
  .person-name .first { color: var(--red); }
  .person-name .last { color: var(--yellow); }
  .contact-list { list-style: none; }
  .contact-list li {
    display: flex; align-items: center; gap: 10px;
    color: var(--white); font-size: 15px; line-height: 25px;
    white-space: nowrap;
  }
  .contact-list svg { width: 14px; height: 14px; flex: none; fill: var(--red); }
  .accent { color: var(--red); }
</style>
</head>
<body>
  <section class="card card--back">
    <div class="back-texture" role="img" aria-label="Faint tone-on-tone repeating brand pattern in deep navy"></div>
    <div class="back-mark">
      <span class="brand-square"></span>
      <span class="brand-name">CORVANE FLOORING</span>
    </div>
  </section>

  <section class="card card--front">
    <div class="front-brand">
      <span class="brand-square"></span>
      <span class="brand-name">CORVANE FLOORING</span>
    </div>
    <div class="divider"></div>
    <div class="contact">
      <p class="person-name"><span class="first">TEODOR</span> <span class="last">VASHKIN</span></p>
      <ul class="contact-list">
        <li><svg viewBox="0 0 16 16"><path d="M2 6c0-2 3-3 6-3s6 1 6 3v1h-3V5.5C10 5 6 5 5 5.5V7H2z M4 8h8l1 5H3z"/></svg>415 555 0142</li>
        <li><svg viewBox="0 0 16 16"><path d="M4 1h8v14H4z M5.5 2.5v10h5v-10z"/></svg>628 555 0187</li>
        <li><svg viewBox="0 0 16 16"><path d="M4 1h8v4H4z M1 6h14v6h-3v3H4v-3H1z M5 10v4h6v-4z"/></svg>628 555 0193</li>
        <li><svg viewBox="0 0 16 16"><path d="M1 3h14v10H1z M2.5 4.5 8 9l5.5-4.5z"/></svg>hello@corvaneflooring.com</li>
        <li><svg viewBox="0 0 16 16"><circle cx="8" cy="8" r="7"/></svg>www.<span class="accent">corvaneflooring</span>.com</li>
      </ul>
    </div>
  </section>
</body>
</html>
```